A design led business card for the construction industry

High-end business card to match logo. White logo on dark grey/off black to the front. Matching dark font on white to back, possibly with logo design again.

We offer construction and project management services to commercial and private clients in the UK. Projetcs range from newbuilds, conversion of listed buildings and refurbishments and extensions of existing homes. Our focus is on quality and attention to detail using the highest skills.

Contact Information for Business Card

Name; Dorian Keble BSc
Position; Project Manager
Mobile; 07962 408 175
Tel; 01632 960457
email; dorian@stonevale.co.uk
web; www.stonevale.co.uk
Address; Oakridge on Wend, KX4 7PW

Colors

Designer to choose only greyscale colors for use in the design.

Requirements
Must have
• To include the below description of the business,

CONSTRUCTION - PROJECT MANAGEMENT
Nice to have
• The posibility of the top back of the card being used as a ruler. So will have a measurement to scale in mm or an architect scale of 1:50
Should not have
• Should not be portrait

```html
<!DOCTYPE html>
<html lang="en">
<head>
<meta charset="utf-8">
<title>Stonevale – Business Card</title>
<link rel="stylesheet" href="https://fonts.googleapis.com/css2?family=Montserrat:wght@400;500&family=Roboto:wght@400;700&display=swap">
<style>
  :root {
    --stage: #2a2a2a;
    --card-dark: #121212;
    --card-light: #ffffff;
    --ink: #111111;
    --ink-soft: #333333;
    --rule: #8a8a8a;
    --tick: #bdbdbd;
    --paper-text: #f2f2f2;
  }
  * { margin: 0; padding: 0; box-sizing: border-box; }
  html, body { width: 1200px; height: 1015px; overflow: hidden; }
  body {
    background: var(--stage);
    font-family: "Roboto", sans-serif;
    position: relative;
  }
  .card {
    position: absolute;
    left: 250px;
    width: 700px;
    height: 405px;
    overflow: hidden;
    box-shadow: 0 10px 28px rgba(0,0,0,0.55);
  }
  .card--front { top: 70px; background: var(--card-dark); }
  .card--back { top: 540px; background: var(--card-light); }

  /* front */
  .ruler { position: absolute; top: 0; left: 0; width: 700px; height: 30px; }
  .front-brand {
    position: absolute;
    left: 0; right: 0; top: 150px;
    text-align: center;
    color: var(--paper-text);
  }
  .front-brand__name {
    font-family: "Montserrat", sans-serif;
    font-weight: 400;
    font-size: 44px;
    letter-spacing: 0.42em;
    padding-left: 0.42em;
  }
  .front-brand__services {
    margin-top: 22px;
    font-family: "Roboto", sans-serif;
    font-size: 16px;
    letter-spacing: 0.14em;
  }

  /* back */
  .back-brand {
    position: absolute;
    left: 40px; top: 70px;
    width: 300px;
    text-align: center;
  }
  .back-brand__mark {
    width: 120px; height: 120px;
    margin: 0 auto;
    border: 4px solid var(--ink);
    border-radius: 6px;
  }
  .back-brand__name {
    margin-top: 22px;
    font-family: "Montserrat", sans-serif;
    font-size: 24px;
    letter-spacing: 0.38em;
    padding-left: 0.38em;
    color: var(--ink);
  }
  .divider {
    position: absolute;
    left: 360px; top: 55px;
    width: 1px; height: 180px;
    background: var(--rule);
  }
  .contact {
    position: absolute;
    left: 385px; top: 55px;
    color: var(--ink);
  }
  .contact__name { font-size: 21px; font-weight: 700; }
  .contact__name span { font-weight: 400; }
  .contact__role { font-size: 17px; color: var(--ink-soft); margin-bottom: 18px; }
  .contact__list { list-style: none; }
  .contact__item {
    display: flex; align-items: center; gap: 8px;
    font-size: 16px; line-height: 24px;
  }
  .contact__item svg { width: 15px; height: 15px; flex: none; }
  .address-band {
    position: absolute;
    left: 0; right: 0; bottom: 0;
    height: 80px;
    background: var(--card-dark);
    color: var(--paper-text);
    font-size: 17px;
    display: flex; align-items: center; justify-content: center;
  }
</style>
</head>
<body>

<section class="card card--front" aria-label="Card front">
  <svg class="ruler" viewBox="0 0 700 30" aria-hidden="true">
    <defs>
      <pattern id="mm-ticks" width="70" height="30" patternUnits="userSpaceOnUse">
        <g stroke="var(--tick)" stroke-width="1">
          <line x1="0.5" y1="0" x2="0.5" y2="22"/>
          <line x1="7.5" y1="0" x2="7.5" y2="8"/>
          <line x1="14.5" y1="0" x2="14.5" y2="8"/>
          <line x1="21.5" y1="0" x2="21.5" y2="8"/>
          <line x1="28.5" y1="0" x2="28.5" y2="8"/>
          <line x1="35.5" y1="0" x2="35.5" y2="14"/>
          <line x1="42.5" y1="0" x2="42.5" y2="8"/>
          <line x1="49.5" y1="0" x2="49.5" y2="8"/>
          <line x1="56.5" y1="0" x2="56.5" y2="8"/>
          <line x1="63.5" y1="0" x2="63.5" y2="8"/>
        </g>
      </pattern>
    </defs>
    <rect x="4" y="0" width="696" height="30" fill="url(#mm-ticks)"/>
  </svg>
  <div class="front-brand">
    <div class="front-brand__name">STONEVALE</div>
    <div class="front-brand__services">CONSTRUCTION - PROJECT MANAGEMENT</div>
  </div>
</section>

<section class="card card--back" aria-label="Card back">
  <div class="back-brand">
    <div class="back-brand__mark"></div>
    <div class="back-brand__name">STONEVALE</div>
  </div>
  <div class="divider"></div>
  <div class="contact">
    <div class="contact__name">DORIAN KEBLE <span>BSc</span></div>
    <div class="contact__role">Project Manager</div>
    <ul class="contact__list">
      <li class="contact__item">
        <svg viewBox="0 0 16 16" aria-hidden="true"><rect x="4" y="1" width="8" height="14" rx="1.5" fill="none" stroke="currentColor" stroke-width="1.6"/><line x1="7" y1="12.5" x2="9" y2="12.5" stroke="currentColor" stroke-width="1.4"/></svg>
        07962 408 175
      </li>
      <li class="contact__item">
        <svg viewBox="0 0 16 16" aria-hidden="true"><path d="M4 2 L6.5 2 L7.5 5 L6 6.5 C7 8.5 8 9.5 9.5 10.5 L11 9 L14 10 L14 12.5 C14 13.5 13 14 12 14 C6.5 13.5 2.5 9.5 2 4 C2 3 2.8 2 4 2 Z" fill="currentColor"/></svg>
        01632 960457
      </li>
      <li class="contact__item">
        <svg viewBox="0 0 16 16" aria-hidden="true"><rect x="1" y="3" width="14" height="10" fill="currentColor"/><polyline points="1,3 8,9 15,3" fill="none" stroke="#fff" stroke-width="1.2"/></svg>
        dorian@stonevale.co.uk
      </li>
      <li class="contact__item">
        <svg viewBox="0 0 16 16" aria-hidden="true"><g fill="none" stroke="currentColor" stroke-width="1.3"><circle cx="8" cy="8" r="6.5"/><ellipse cx="8" cy="8" rx="3" ry="6.5"/><line x1="1.5" y1="8" x2="14.5" y2="8"/></g></svg>
        www.stonevale.co.uk
      </li>
    </ul>
  </div>
  <div class="address-band">Oakridge on Wend, KX4 7PW</div>
</section>

</body>
</html>
```